Need Website Design for Non-Profit Veteran Site

I am looking for a very talented creative website designer for a modern feel. I'll give a little bit of guidance around what I am looking for and then your creative juices should kick in and design away. I have already purchased the domain but will need hosting (at least temporarily) and the creative design work done.The website domain is militarydocs.orgI am looking to attract current and veteran military providers (doctors, nurse practitioners, physician assistants, etc) to join and signup for membership. They would pay a yearly fee to join. Would need membership categories $135 for Provider, $55 Student, $100 for Retired, and Organization (Organization would be broken down into Less than 100 ($200), 100-249 ($250), 250-499 ($300), 500-999 ($400), 1,000-2,999 ($500), and 3,000 ($700). Would need Benefit built out and would need to accept money through CoinVane and other means. Since it's a new organization just starting, would also need a Donate button to get people to donate if they want any amount they would like. The second part of the website is that once they join, they will have acess to a list of all other providers who have registered within the website (not exportable) so they can connect with one another. If they want to see contact information this will be included in their fee as a benefit to socialize with one another. As part of the website, there will be another Veteran's portal so veterans who would like to connect with a provider around a particular speciality can reach out and request help from the doctor writing a nexus letter or letter to support the veteran who is filing a claim with the BQ. Veterans would pay a yearly sign-up fee of $30.00 and would need their membership benefits displayed. They would have access to a list of veterans in their region by state and distance, and can reach out to doctors to get their help. If a doctor and veteran agree, sharable inforamtion of medical hipaa documents can be exchanged via the website. The physician and veteran can negotiate a fee through the website only and share their details. This is a separate fee for this type of process between the provider and veteran. We will collect a $250 fee for admin on each of these and each project the veteran does with the provider will cost $450 (so essentially the doctor gets paid $450 and i get $250.00. This model could be changed over time as we start to test this out). A good example of 50% of what I'm looking for is something like the following website: https://www.lpkt.org/ It has some of the features but not all and my site should be more modernized to attract the veteran and military providers.

Target Market(s)

Current and retired military providers and veterans

Industry/Entity Type

Non Profit

Number of Pages Required

1 page

Requirements
Must have
• Military Design
• Modern Feel (Example templates for feel -https://quillmoth.com/free-photoshop-psd-web-design-template/)
• Donation box
• Stuff mentioned in the description)
Nice to have
• Open to feedback
Should not have
• Open to feedback

```html
<!DOCTYPE html>
<html lang="en">
<head>
<meta charset="utf-8">
<title>Harborwell — Non-Profit for Military Providers</title>
<link rel="stylesheet" href="https://fonts.googleapis.com/css2?family=Frank+Ruhl+Libre:wght@400;500&family=Merriweather:wght@400;700&display=swap">
<style>
:root{
  --red:#c8343b;
  --blue:#0b5893;
  --navy:#0c2a45;
  --ink:#1b1b1b;
  --muted:#666;
  --camo:#ececec;
  --card:#e4e4e4;
  --white:#fff;
  --heading:"Frank Ruhl Libre", Georgia, serif;
  --body:"Merriweather", Georgia, serif;
}
*{box-sizing:border-box;margin:0;padding:0}
html,body{width:1200px;height:3130px;overflow:hidden}
body{font-family:var(--body);color:var(--ink);background:var(--white);position:relative}
a{color:inherit;text-decoration:none}
.btn{display:inline-flex;align-items:center;justify-content:center;font-family:var(--body);font-size:12px;color:var(--white)}
.btn--red{background:var(--red)}
.btn--blue{background:var(--blue)}

/* header */
.site-header{height:125px;background:linear-gradient(180deg,#e9e9e9,#dcdcdc);display:flex;align-items:center;padding:0 48px 0 75px;justify-content:space-between}
.brand{font-family:var(--heading);font-size:46px;color:var(--red);font-weight:400;padding-bottom:14px}
.header-actions{display:flex;align-items:center;gap:16px;padding-bottom:14px}
.phone{display:flex;align-items:center;gap:6px;font-family:var(--heading);font-size:21px;color:#333;margin-right:4px}
.header-actions .btn{height:38px}
.btn--join{width:72px}
.btn--signup{width:90px}

.main-nav{height:69px;background:var(--blue);display:flex;align-items:center;padding-left:120px;gap:0}
.main-nav a{color:var(--white);font-family:var(--heading);font-size:17px;margin-right:57px}

/* hero */
.hero{position:relative;height:463px;background:linear-gradient(100deg,#5e6a4a 0%,#7e806a 30%,#3f5a37 60%,#2d4a2b 100%);text-align:center;color:var(--white)}
.hero-title{position:absolute;top:140px;left:0;right:0;font-family:var(--heading);font-weight:400;font-size:66px}
.hero-sub{position:absolute;top:222px;left:0;right:0;font-size:14px}
.hero-actions{position:absolute;top:262px;left:0;right:0;display:flex;justify-content:center;gap:14px}
.hero-actions .btn{width:177px;height:38px;font-size:12px}
.hero-dots{position:absolute;top:413px;left:0;right:0;display:flex;justify-content:center;gap:10px}
.hero-dots span{width:7px;height:7px;border-radius:50%;background:rgba(255,255,255,.55)}
.hero-dots span:first-child{background:var(--white)}

.section-title{font-family:var(--heading);font-weight:400;font-size:42px;text-align:center}
.rule{width:156px;height:2px;background:var(--blue);margin:20px auto 0}

/* services */
.services{height:537px;background:var(--camo);padding-top:60px}
.service-list{display:flex;gap:29px;margin:46px 0 0 67px}
.service{width:336px}
.service-photo{height:205px}
.service-label{height:65px;display:flex;align-items:center;gap:12px;padding-left:22px;color:var(--white);font-family:var(--heading);font-size:20px}
.service--red .service-label{background:var(--red)}
.service--blue .service-label{background:var(--blue)}

/* plans */
.plans{height:469px;background:var(--white);padding-top:57px}
.plan-list{display:flex;gap:27px;margin:46px 0 0 67px}
.plan{width:246px;height:229px;background:var(--card);text-align:center;padding-top:28px}
.plan--featured{background:var(--red);color:var(--white)}
.plan-name{font-family:var(--heading);font-size:27px;font-weight:400}
.plan-price{font-family:var(--heading);font-size:42px;line-height:1}
.plan-price sup{font-size:20px;vertical-align:-6px}
.plan-note{font-size:8px;font-weight:700;margin-top:-2px}
.plan-desc{font-size:9px;line-height:1.55;color:#777;width:180px;margin:8px auto 0}
.plan--featured .plan-desc{color:#fbe7e8}
.plan .btn{width:120px;height:30px;margin-top:12px;font-size:11px}
.plan--featured .btn{background:#f1f1f1;color:#333}

/* news */
.news{height:783px;background:var(--camo);padding-top:64px}
.news-grid{display:grid;grid-template-columns:523px 523px;column-gap:21px;row-gap:56px;margin:56px 0 0 67px}
.news-item{display:flex;gap:12px}
.news-photo{width:219px;height:182px;flex:none}
.news-date{font-size:10px;font-weight:700;color:var(--blue)}
.news-title{font-family:var(--heading);font-weight:400;font-size:18px;line-height:1.4;margin-top:4px}
.news-rule{width:66px;height:2px;background:var(--blue);margin:12px 0 14px}
.news-text{font-size:8.5px;line-height:1.75;color:#777}
.news-more{display:inline-block;margin-top:12px;font-size:10px;color:var(--red);text-decoration:underline}
.view-more{display:flex;justify-content:center;margin-top:54px}
.view-more a{width:204px;height:40px;border:1px solid #999;display:flex;align-items:center;justify-content:center;font-size:11px;color:#333;background:#f3f3f3}

/* donation */
.donation{height:371px;background:var(--navy);color:var(--white);text-align:center;padding-top:62px}
.donation .section-title{font-size:44px}
.donation p{width:660px;margin:30px auto 0;font-size:11px;line-height:2.2;color:#dfe6ee}
.donation .btn{width:172px;height:37px;margin-top:20px}

/* footer */
.site-footer{height:313px;position:relative;background:var(--white)}
.footer-brand{position:absolute;left:67px;top:55px;font-family:var(--heading);font-size:34px;color:var(--red)}
.footer-about{position:absolute;left:67px;top:112px;width:300px;font-size:9px;line-height:1.75;color:#555}
.footer-links{position:absolute;top:60px;list-style:none;font-size:11px;line-height:20px;color:#333}
.footer-links--main{left:472px}
.footer-links--legal{left:693px}
.footer-cta{position:absolute;left:908px;top:63px;display:flex;flex-direction:column;gap:13px}
.footer-cta .btn{width:165px;height:38px}
.social{position:absolute;left:922px;top:170px;display:flex;gap:7px}
.social span{width:22px;height:22px;border-radius:50%}
.footer-rule{position:absolute;left:67px;right:67px;top:257px;height:1px;background:#ccc}
.copyright{position:absolute;top:280px;left:0;right:0;text-align:center;font-size:10px;color:#444}
</style>
</head>
<body>

<header class="site-header">
  <div class="brand">Harborwell</div>
  <div class="header-actions">
    <span class="phone">
      <svg width="18" height="18" viewBox="0 0 24 24"><path d="M6.6 10.8a15 15 0 0 0 6.6 6.6l2.2-2.2a1 1 0 0 1 1-.25 11.4 11.4 0 0 0 3.6.57 1 1 0 0 1 1 1V20a1 1 0 0 1-1 1A17 17 0 0 1 3 4a1 1 0 0 1 1-1h3.5a1 1 0 0 1 1 1c0 1.25.2 2.45.57 3.57a1 1 0 0 1-.25 1z" fill="var(--red)"/></svg>
      1-800-555-0142
    </span>
    <a class="btn btn--red btn--join" href="#">Join Us</a>
    <a class="btn btn--blue btn--signup" href="#">Sign Up</a>
  </div>
</header>

<nav class="main-nav">
  <a href="#">Home</a><a href="#">About Us</a><a href="#">Services</a><a href="#">Membership</a><a href="#">FAQs</a><a href="#">Testimonials</a><a href="#">News</a><a href="#">Contact Us</a>
</nav>

<section class="hero" role="img" aria-label="Service member in camouflage holding a small national flag while embracing her child, trees behind">
  <h1 class="hero-title">Harborwell</h1>
  <p class="hero-sub">Neque porro quisquam est qui dolorem ipsum quia dolor</p>
  <div class="hero-actions">
    <a class="btn btn--red" href="#">Donate Now</a>
    <a class="btn btn--blue" href="#">Veterans Sign-Up</a>
  </div>
  <div class="hero-dots"><span></span><span></span><span></span><span></span></div>
</section>

<section class="services">
  <h2 class="section-title">What We Do?</h2>
  <div class="rule"></div>
  <div class="service-list">
    <div class="service service--red">
      <div class="service-photo" role="img" aria-label="Doctor in a white coat at a desk" style="background:linear-gradient(120deg,#c8b48a,#e6dccb 55%,#b9a27a)"></div>
      <div class="service-label">
        <svg width="22" height="26" viewBox="0 0 22 26" fill="none" stroke="#fff" stroke-width="2"><path d="M4 2v7a5 5 0 0 0 10 0V2"/><path d="M9 14v5a5 5 0 0 0 10 0v-3"/><circle cx="19" cy="13" r="2"/></svg>
        Doctors
      </div>
    </div>
    <div class="service service--blue">
      <div class="service-photo" role="img" aria-label="Nurse practitioner talking with an elderly patient" style="background:linear-gradient(120deg,#a89070,#d8cdb8 50%,#8d7a64)"></div>
      <div class="service-label">
        <svg width="22" height="26" viewBox="0 0 22 26" fill="#fff"><path d="M5 0h12l-3 8H8z"/><circle cx="11" cy="16" r="8"/><circle cx="11" cy="16" r="4" fill="var(--blue)"/></svg>
        Nurse Practitioners
      </div>
    </div>
    <div class="service service--blue">
      <div class="service-photo" role="img" aria-label="Physician assistant greeting a patient" style="background:linear-gradient(120deg,#dfe3e8,#f2f2f2 50%,#b8bcc4)"></div>
      <div class="service-label">
        <svg width="24" height="24" viewBox="0 0 24 24" fill="#fff"><path d="M10 0h4v8.5l7.4-4.3 2 3.5L16 12l7.4 4.3-2 3.5L14 15.5V24h-4v-8.5l-7.4 4.3-2-3.5L8 12 .6 7.7l2-3.5L10 8.5z"/></svg>
        Physician Assistants
      </div>
    </div>
  </div>
</section>

<section class="plans">
  <h2 class="section-title">Membership Plans</h2>
  <div class="rule"></div>
  <div class="plan-list">
    <div class="plan plan--featured">
      <h3 class="plan-name">Provider</h3>
      <div class="plan-price"><sup>$</sup>135</div>
      <p class="plan-desc">Neque porro quisquam est qui dolorem ipsum quia dolor sit amet</p>
      <a class="btn" href="#">Sign-Up</a>
    </div>
    <div class="plan">
      <h3 class="plan-name">Retired</h3>
      <div class="plan-price"><sup>$</sup>100</div>
      <p class="plan-desc">Neque porro quisquam est qui dolorem ipsum quia dolor sit amet</p>
      <a class="btn btn--blue" href="#">Sign-Up</a>
    </div>
    <div class="plan">
      <h3 class="plan-name">Student</h3>
      <div class="plan-price"><sup>$</sup>55</div>
      <p class="plan-desc">Neque porro quisquam est qui dolorem ipsum quia dolor sit amet</p>
      <a class="btn btn--blue" href="#">Sign-Up</a>
    </div>
    <div class="plan">
      <h3 class="plan-name">Organization</h3>
      <div class="plan-price"><sup>$</sup>100</div>
      <div class="plan-note">Less Than</div>
      <p class="plan-desc" style="margin-top:2px">Neque porro quisquam est qui dolorem ipsum quia dolor sit amet</p>
      <a class="btn btn--blue" href="#">Sign-Up</a>
    </div>
  </div>
</section>

<section class="news">
  <h2 class="section-title">Latest News</h2>
  <div class="news-grid">
    <article class="news-item">
      <div class="news-photo" role="img" aria-label="Volunteers at a blood donation drive" style="background:linear-gradient(120deg,#7b8fa0,#c9a6a0 50%,#6a5b56)"></div>
      <div>
        <div class="news-date">February 13th 2018</div>
        <h3 class="news-title">Neque porro quisquam est qui dolorem ipsum quia dolor sit amet....</h3>
        <div class="news-rule"></div>
        <p class="news-text">Sed ut perspiciatis unde omnis iste natus error sit voluptatem accusantium doloremque laudantium, totam rem aperiam, eaque ipsa quae ab illo inventore</p>
        <a class="news-more" href="#">Read More</a>
      </div>
    </article>
    <article class="news-item">
      <div class="news-photo" role="img" aria-label="Volunteers serving food to seniors" style="background:linear-gradient(120deg,#5f6f4f,#b9ad98 50%,#7a6a58)"></div>
      <div>
        <div class="news-date">February 13th 2018</div>
        <h3 class="news-title">Neque porro quisquam est qui dolorem ipsum quia dolor sit amet....</h3>
        <div class="news-rule"></div>
        <p class="news-text">Sed ut perspiciatis unde omnis iste natus error sit voluptatem accusantium doloremque laudantium, totam rem aperiam, eaque ipsa quae ab illo inventore</p>
        <a class="news-more" href="#">Read More</a>
      </div>
    </article>
    <article class="news-item">
      <div class="news-photo" role="img" aria-label="Arm with a green bandage after donating blood" style="background:linear-gradient(120deg,#6f7d5c,#c9b8a4 50%,#8a7563)"></div>
      <div>
        <div class="news-date">February 13th 2018</div>
        <h3 class="news-title">Neque porro quisquam est qui dolorem ipsum quia dolor sit amet....</h3>
        <div class="news-rule"></div>
        <p class="news-text">Sed ut perspiciatis unde omnis iste natus error sit voluptatem accusantium doloremque laudantium, totam rem aperiam, eaque ipsa quae ab illo inventore</p>
        <a class="news-more" href="#">Read More</a>
      </div>
    </article>
    <article class="news-item">
      <div class="news-photo" role="img" aria-label="Soldier carrying a wooden crate of donated groceries" style="background:linear-gradient(120deg,#5c5e4c,#a37b55 55%,#6e5238)"></div>
      <div>
        <div class="news-date">February 13th 2018</div>
        <h3 class="news-title">Neque porro quisquam est qui dolorem ipsum quia dolor sit amet....</h3>
        <div class="news-rule"></div>
        <p class="news-text">Sed ut perspiciatis unde omnis iste natus error sit voluptatem accusantium doloremque laudantium, totam rem aperiam, eaque ipsa quae ab illo inventore</p>
        <a class="news-more" href="#">Read More</a>
      </div>
    </article>
  </div>
  <div class="view-more"><a href="#">View More News</a></div>
</section>

<section class="donation">
  <h2 class="section-title">Donation</h2>
  <p>Sed ut perspiciatis unde omnis iste natus error sit voluptatem accusantium doloremque laudantium, totam rem aperiam, eaque ipsa quae ab illo inventore veritatis et quasi architecto beatae vitae dicta sunt explicabo. Nemo enim ipsam voluptatem quia voluptas sit aspernatur aut odit aut fugit, sed quia</p>
  <a class="btn btn--red" href="#">Donate Now</a>
</section>

<footer class="site-footer">
  <div class="footer-brand">Harborwell</div>
  <p class="footer-about">Sed ut perspiciatis unde omnis iste natus error sit voluptatem accusantium doloremque laudantium, totam rem aperiam, eaque ipsa quae ab illo inventore veritatis et quasi architecto beatae vitae dicta sunt explicabo.</p>
  <ul class="footer-links footer-links--main">
    <li>Home</li><li>About Us</li><li>Services</li><li>Membership</li><li>FAQs</li><li>Testimonials</li><li>News</li><li>Contact Us</li>
  </ul>
  <ul class="footer-links footer-links--legal">
    <li>Terms of Use</li><li>Privacy Policy</li>
  </ul>
  <div class="footer-cta">
    <a class="btn btn--blue" href="#">Sign Up</a>
    <a class="btn btn--red" href="#">Join Us</a>
  </div>
  <div class="social" aria-label="Social links">
    <span style="background:#3b5a9a"></span><span style="background:#c8343b"></span><span style="background:#2fa3d9"></span><span style="background:#1a6fa6"></span><span style="background:#d24b3e"></span>
  </div>
  <div class="footer-rule"></div>
  <div class="copyright">© 2018 Company Name | All Rights Reserved</div>
</footer>

</body>
</html>
```